Social Media Graphics - Oakline Push REVISED

Create 6-7 individual social media graphics (square size) to encourage folks to join our online course called:

The Harvest Ledger Circle
How to Launch a Multi-Million Business From Scratch
Sign Up Today!

IMPORTANT: Make the largest and most prominent text on the graphic be: How to Launch a Multi-Million Business From Scratch

For the color scheme of the graphics, let's try a blue color palette; make sure the graphics appeal to both men and women

Make sure each graphic contains 1 of the 3 pics attached (crop pic as needed); and make sure one of the graphics is all TEXT only.

Target Market(s)

men and women looking to start a business

Industry/Entity Type

Entrepreneurship

Colors
0054AA
0677BA
7BADD7
CADEEF
E8F1F8

Requirements
Must have
• All the text and use the 3 pics provided; one graphic can be all text; Simple, modern design that's easy to read

```html
<!DOCTYPE html>
<html lang="en">
<head>
<meta charset="utf-8">
<title>The Harvest Ledger Circle – Social Graphic</title>
<link rel="stylesheet" href="https://fonts.googleapis.com/css2?family=Bebas+Neue&family=Montserrat:wght@500&family=Poppins:wght@700;800&display=swap">
<style>
  :root {
    --stage: #5f5f5f;
    --navy-deep: #04142f;
    --navy: #0a2c5e;
    --navy-light: #0f3f80;
    --cyan: #17bdf0;
    --cyan-box: #1a9ccc;
    --white: #ffffff;
    --button-top: #1fa6d6;
    --button-bottom: #0cc3f4;
  }
  * { margin: 0; padding: 0; box-sizing: border-box; }
  html, body {
    width: 1195px;
    height: 1200px;
    overflow: hidden;
    background: var(--stage);
  }
  .graphic {
    position: absolute;
    left: 100px;
    top: 89px;
    width: 996px;
    height: 994px;
    overflow: hidden;
    background: radial-gradient(ellipse at 75% 25%, var(--navy-light) 0%, var(--navy) 40%, var(--navy-deep) 100%);
  }
  .growth-art {
    position: absolute;
    left: 486px;
    top: 32px;
    width: 478px;
    height: 263px;
    border-radius: 12px;
    background: radial-gradient(ellipse at 60% 60%, rgba(70, 170, 200, 0.55) 0%, rgba(30, 110, 170, 0.25) 55%, rgba(10, 44, 94, 0) 80%);
  }
  .horizon-glow {
    position: absolute;
    left: 480px;
    top: 294px;
    width: 516px;
    height: 4px;
    border-radius: 2px;
    background: linear-gradient(90deg, rgba(23, 189, 240, 0) 0%, #2a8dff 30%, #2a8dff 100%);
    box-shadow: 0 0 12px #2a8dff;
  }
  .base-shape {
    position: absolute;
    left: 0;
    top: 0;
    width: 996px;
    height: 994px;
  }
  .hosts-photo {
    position: absolute;
    left: 526px;
    top: 320px;
    width: 470px;
    height: 674px;
    border-radius: 160px 120px 0 0;
    background: linear-gradient(160deg, #2b1c22 0%, #6b3a3e 35%, #c94a5e 65%, #1a1216 100%);
    z-index: 1;
  }
  .text {
    position: absolute;
    line-height: 1;
    white-space: nowrap;
    z-index: 2;
  }
  .course-name {
    left: 66px;
    top: 60px;
    font-family: "Bebas Neue", sans-serif;
    font-weight: 400;
    font-size: 79px;
    color: var(--white);
    letter-spacing: -0.5px;
  }
  .course-name .highlight {
    background: var(--cyan-box);
    padding: 2px 6px 0;
  }
  .how-to {
    left: 64px;
    top: 205px;
    font-family: "Montserrat", sans-serif;
    font-weight: 500;
    font-size: 72px;
    color: var(--cyan);
  }
  .launch {
    left: 58px;
    top: 250px;
    font-family: "Bebas Neue", sans-serif;
    font-size: 228px;
    color: var(--white);
    letter-spacing: -2px;
  }
  .multi-million {
    left: 68px;
    top: 464px;
    font-family: "Bebas Neue", sans-serif;
    font-size: 90px;
    color: var(--cyan);
  }
  .business {
    left: 66px;
    top: 540px;
    font-family: "Poppins", sans-serif;
    font-weight: 800;
    font-size: 94px;
    color: var(--white);
    letter-spacing: -1px;
  }
  .from-scratch {
    left: 72px;
    top: 636px;
    font-family: "Bebas Neue", sans-serif;
    font-size: 100px;
    color: var(--cyan);
  }
  .sign-up {
    position: absolute;
    left: 69px;
    top: 867px;
    width: 301px;
    height: 72px;
    border-radius: 16px;
    background: linear-gradient(180deg, var(--button-top), var(--button-bottom));
    display: flex;
    align-items: center;
    justify-content: center;
    font-family: "Poppins", sans-serif;
    font-weight: 700;
    font-size: 28px;
    color: var(--white);
    letter-spacing: -0.5px;
    z-index: 2;
  }
</style>
</head>
<body>
  <main class="graphic">
    <div class="growth-art" role="img" aria-label="Illustration of a sprouting plant growing from stacks of coins beside a rising bar chart"></div>
    <div class="horizon-glow"></div>

    <svg class="base-shape" viewBox="0 0 996 994" aria-hidden="true">
      <path d="M0 787 C 60 830, 130 848, 190 845 C 290 840, 360 790, 386 720 C 420 800, 470 880, 540 911 L 540 994 L 0 994 Z" fill="#ffffff"/>
    </svg>

    <div class="hosts-photo" role="img" aria-label="Photo of the two course hosts smiling, a woman in a red dress with arms crossed and a man in a black shirt"></div>

    <h1 class="text course-name">THE <span class="highlight">HARVEST LEDGER</span> CIRCLE</h1>
    <p class="text how-to">HOW TO</p>
    <p class="text launch">LAUNCH</p>
    <p class="text multi-million">A MULTI-MILLION</p>
    <p class="text business">BUSINESS</p>
    <p class="text from-scratch">FROM SCRATCH</p>

    <a class="sign-up">SIGN UP TODAY!</a>
  </main>
</body>
</html>
```